Australian Trucking Company Requires Professional Looking Stationary

We require a professional looking stationary design that incorporates our newly designed logo.

Our business, called "Brell Haulage Contracting", provides contracting work, transport and logistics to business in Western Australia particularly with links to the mining sector.

We are a small business looking to expand and our new logo and our new stationary will help develop our brand image in our market place.

Target Market(s)

Businesses and Corporation with links to the Mining Sector

Industry/Entity Type

Small Business

Requirements
Must have
• The letterhead must have the following details:
The new logo

Text saying: "Brell Holdings Pty Ltd (ACN 582 316 907) ATF The Brell Discretionary Trust T/AS"
"ABN 71 834 209 553"
Address "P.O Box 817 Wattlegrove WA, 6958"
Phone: 08 9352 7140
Email: brellhaul@mailbox-example.com.au

The text on the letterhead should be editable as the details are likely to change in the near future. Provision should be made for a website address all though one isn't available at the moment.

The styling, layout and font text is entirely up to the designer.

```html
<!DOCTYPE html>
<html lang="en">
<head>
<meta charset="utf-8">
<title>Brell Haulage Contracting – Business Card</title>
<link rel="stylesheet" href="https://fonts.googleapis.com/css2?family=Open+Sans:wght@400;600;700&display=swap">
<style>
  :root {
    --bg: #e8e5e1;
    --white: #ffffff;
    --red: #c4121c;
    --red-deep: #8e0c13;
    --red-bright: #e8202a;
    --grey: #a9abad;
    --grey-text: #555759;
    --ink: #2f3133;
    --faint: rgba(255, 255, 255, 0.55);
  }
  * { margin: 0; padding: 0; box-sizing: border-box; }
  html, body {
    width: 1200px; height: 407px; overflow: hidden;
    background: var(--bg);
    font-family: "Open Sans", Arial, sans-serif;
  }
  .canvas { position: relative; width: 1200px; height: 407px; }
  .card {
    position: absolute; top: 60px; width: 504px; height: 288px; overflow: hidden;
  }
  .card--front { left: 58px; background: var(--white); }
  .card--back {
    left: 638px;
    background: radial-gradient(ellipse at 50% 48%, var(--red-bright) 0%, var(--red) 45%, var(--red-deep) 100%);
    color: var(--white); text-align: center;
  }
  .card__waves { position: absolute; inset: 0; }

  .brand { position: absolute; left: 30px; top: 26px; display: flex; align-items: center; gap: 16px; }
  .brand__dot { width: 58px; height: 58px; border-radius: 50%; background: var(--grey); }
  .brand__name {
    color: var(--red); font-weight: 700; font-size: 25px; line-height: 1.05;
    text-transform: uppercase; letter-spacing: 0.5px;
  }

  .abn { position: absolute; left: 29px; top: 152px; font-size: 12.5px; color: var(--grey-text); }

  .person { position: absolute; right: 22px; top: 154px; text-align: right; color: var(--white); }
  .person__name { font-size: 16px; font-weight: 700; line-height: 1.2; }
  .person__title { font-size: 12.5px; line-height: 1.3; }

  .contact { position: absolute; right: 17px; top: 203px; list-style: none; color: var(--white); font-size: 11px; }
  .contact li { display: flex; justify-content: flex-end; align-items: center; gap: 8px; height: 16px; }
  .contact li.contact__address { margin-top: 8px; }
  .contact svg { width: 11px; height: 11px; fill: var(--white); flex: none; }

  .legal { position: absolute; top: 29px; left: 0; right: 0; font-size: 10.5px; }
  .back-mark {
    position: absolute; left: 0; right: 0; top: 112px;
    font-size: 30px; font-weight: 700; line-height: 1.1; text-transform: uppercase;
    color: var(--faint);
  }
  .website { position: absolute; left: 0; right: 0; bottom: 12px; font-size: 13px; font-weight: 700; letter-spacing: 2.5px; }
</style>
</head>
<body>
<main class="canvas">
  <section class="card card--front">
    <svg class="card__waves" viewBox="0 0 504 288" preserveAspectRatio="none" aria-hidden="true">
      <defs>
        <radialGradient id="redGlow" cx="0.6" cy="0.75" r="0.7">
          <stop offset="0" stop-color="#e8202a"/>
          <stop offset="0.5" stop-color="#c4121c"/>
          <stop offset="1" stop-color="#8e0c13"/>
        </radialGradient>
      </defs>
      <path d="M0,212 C70,250 160,235 250,170 C330,115 420,100 504,98 L504,116 C420,118 350,135 280,180 C190,240 90,272 0,250 Z" fill="#a9abad"/>
      <path d="M0,262 C110,268 190,200 280,158 C360,122 440,118 504,124 L504,288 L0,288 Z" fill="url(#redGlow)"/>
      <path d="M20,272 C130,270 200,215 290,172 C360,140 420,132 480,130" fill="none" stroke="#ffffff" stroke-width="1.6"/>
    </svg>

    <div class="brand">
      <span class="brand__dot"></span>
      <p class="brand__name">Brell<br>Haulage<br>Contracting</p>
    </div>

    <p class="abn">ABN 71 834 209 553</p>

    <div class="person">
      <p class="person__name">Your Name</p>
      <p class="person__title">Title</p>
    </div>

    <ul class="contact">
      <li>08 9352 7140
        <svg viewBox="0 0 24 24"><path d="M6.6 10.8a15.1 15.1 0 0 0 6.6 6.6l2.2-2.2a1 1 0 0 1 1-.25 11.4 11.4 0 0 0 3.6.57 1 1 0 0 1 1 1V20a1 1 0 0 1-1 1A17 17 0 0 1 3 4a1 1 0 0 1 1-1h3.5a1 1 0 0 1 1 1c0 1.25.2 2.45.57 3.57a1 1 0 0 1-.25 1Z"/></svg>
      </li>
      <li>brellhaul@mailbox-example.com.au
        <svg viewBox="0 0 24 24"><path d="M2 5h20v14H2z M2 5l10 8 10-8" /></svg>
      </li>
      <li>www.brellhaulage-example.com
        <svg viewBox="0 0 24 24"><circle cx="12" cy="12" r="10"/></svg>
      </li>
      <li class="contact__address">P.O Box 817 Wattlegrove WA, 6958
        <svg viewBox="0 0 24 24"><path d="M12 3 2 12h3v9h5v-6h4v6h5v-9h3Z"/></svg>
      </li>
    </ul>
  </section>

  <section class="card card--back">
    <p class="legal">Brell Holdings Pty Ltd (ACN 582 316 907) ATF The Brell Discretionary Trust T/AS</p>
    <p class="back-mark">Brell Haulage<br>Contracting</p>
    <p class="website">www.brellhaulage-example.com</p>
  </section>
</main>
</body>
</html>
```